Meridale Partners Website

Meridale Partners (MP) provide Analytics & Enterprise Performance Management (EPM) advisory & consultancy services. We are passionate about data and making a difference for our clients by working in partnership with them, helping them on their journey to becoming an Meridale Partner. We deliver insights which give our clients a competitive edge and a much deeper understanding of their organisation.

We need a website which shows who we are, what we do and how we do it.

www.meridale-partners.example is our very basic website at the moment. We want to completely revamp it with a corporate look

```html
<!DOCTYPE html>
<html lang="en">
<head>
<meta charset="utf-8">
<title>Meridale Partners</title>
<link rel="stylesheet" href="https://fonts.googleapis.com/css2?family=Montserrat:wght@300;400;500;600;700;800&family=Roboto:wght@400&display=swap">
<style>
:root{
  --navy:#1d3c55;
  --navy-deep:#183349;
  --button:#2a5470;
  --ink:#1e3d56;
  --text:#555d66;
  --mist:#dfe3e8;
  --pale:#eef1f4;
  --white:#ffffff;
  --footer-text:#dbe4ec;
}
*{margin:0;padding:0;box-sizing:border-box}
html,body{width:1200px;height:3465px;overflow:hidden;background:var(--white)}
body{position:relative;font-family:'Montserrat',sans-serif;color:var(--text)}
.abs{position:absolute}
.brand{display:flex;align-items:center;gap:14px;color:var(--ink);font-weight:700;font-size:29px;line-height:1.05;letter-spacing:.5px;text-transform:uppercase}
.brand-dot{width:54px;height:54px;border-radius:50%;background:var(--ink);flex:none}
.btn{display:flex;align-items:center;justify-content:center;background:var(--button);color:var(--white);font-weight:700;text-transform:uppercase;border-radius:40px}
.section-title{color:var(--ink);font-weight:800;font-size:56px;letter-spacing:1px;text-transform:uppercase;line-height:1}

/* header */
.header-phone{left:738px;top:44px;display:flex;align-items:center;gap:12px;color:var(--ink);font-weight:700;font-size:30px}
.menu-bars{left:1016px;top:52px;width:38px;height:32px;display:flex;flex-direction:column;justify-content:space-between}
.menu-bars span{height:6px;background:var(--ink);border-radius:1px}

/* hero */
.hero-photo{left:0;top:120px;width:720px;height:452px;background:linear-gradient(100deg,#c9d2da 0%,#5c7892 30%,#1f3b58 48%,#aab9c6 70%,rgba(255,255,255,0) 100%)}
.hero-title{left:672px;top:192px;color:var(--ink);font-weight:800;font-size:57px;line-height:.84;text-transform:uppercase}
.hero-sub{left:672px;top:302px;color:var(--ink);font-weight:600;font-size:25px;line-height:46px;text-transform:uppercase}
.hero-btn{left:672px;top:402px;width:170px;height:62px;font-size:16px}
.slider-dots{left:1122px;top:300px;display:flex;flex-direction:column;gap:12px}
.slider-dots span{width:9px;height:9px;border-radius:50%;background:#c3c7cc}
.slider-dots span.active{background:var(--ink)}

/* about */
.about{left:0;top:572px;width:1200px;height:443px;background:var(--mist)}
.about-art{left:143px;top:600px;width:387px;height:387px;border-radius:50%;background:radial-gradient(circle at 40% 40%,#3d6583,#1b3a52 70%)}
.about-title{left:594px;top:655px}
.about-text{left:594px;top:730px;width:466px;font-size:13.6px;line-height:24px;font-weight:400}
.about-btn{left:594px;top:875px;width:137px;height:50px;font-size:14px}

/* what we do */
.wwd-panel{left:0;top:1015px;width:321px;height:613px;background:linear-gradient(180deg,#1f4260,#173550)}
.wwd-title{left:387px;top:1127px}
.wwd-arrows{left:993px;top:1136px;display:flex;gap:4px}
.service-card{top:1227px;width:291px;height:306px;display:flex;align-items:flex-end;justify-content:center;padding:0 20px 34px;color:var(--white);font-weight:700;font-size:18px;line-height:25px;text-align:center;text-transform:uppercase}
.card-advise{left:143px;background:linear-gradient(180deg,#d7dce1 0%,#6c7580 45%,#10161d 100%)}
.card-design{left:453px;background:linear-gradient(180deg,#1f4466 0%,#17304a 55%,#0a1420 100%)}
.card-optimise{left:764px;background:linear-gradient(180deg,#2f5a92 0%,#1a3560 55%,#0b1424 100%)}

/* how we do it */
.how-photo{left:600px;top:1628px;width:600px;height:780px;background:linear-gradient(120deg,#8c7a68 0%,#b58a5f 35%,#3c3a3c 75%,#2a2b30 100%)}
.how-tab{left:143px;top:1708px;width:487px;height:82px;background:var(--white)}
.how-title{left:163px;top:1724px}
.step{left:146px;width:440px;height:100px}
.step-mark{position:absolute;left:16px;top:10px;width:64px;height:64px;background:var(--navy);transform:rotate(45deg)}
.step-num{position:absolute;left:0;top:10px;width:96px;height:64px;display:flex;align-items:center;justify-content:center;color:var(--white);font-weight:800;font-size:27px}
.step h3{position:absolute;left:106px;top:-4px;width:320px;color:var(--ink);font-weight:700;font-size:19px;line-height:24px;text-transform:uppercase}
.step p{position:absolute;left:106px;width:320px;font-size:15px;line-height:23px;font-weight:400;color:#5d646b}

/* contact */
.contact{left:0;top:2408px;width:1200px;height:600px;background:linear-gradient(180deg,#f4f6f8,#e8edf1)}
.contact-title{left:0;top:2496px;width:1200px;text-align:center}
.field{background:var(--white);font-family:'Roboto',sans-serif;font-size:15.5px;color:#555;padding:18px 22px}
.submit{left:532px;top:2867px;width:136px;height:50px;font-size:14px}

/* footer */
.footer{left:0;top:3008px;width:1200px;height:457px;background:var(--navy)}
.footer .brand{color:var(--white);font-size:24px;font-weight:600}
.footer .brand-dot{width:44px;height:44px;background:var(--white)}
.foot-contact{left:177px;top:3178px;display:flex;align-items:center;gap:12px;color:var(--white)}
.foot-contact small{display:block;font-size:18px;font-weight:400}
.foot-contact strong{display:block;font-size:24px;font-weight:700}
.foot-address{left:177px;top:3255px;color:var(--footer-text);font-size:13.5px;line-height:25px}
.foot-address a{color:var(--white);font-weight:700;text-decoration:underline}
.foot-heading{color:var(--white);font-weight:700;font-size:16px;text-transform:uppercase}
.quick-links{left:528px;top:3128px;list-style:none;color:var(--white);font-size:13.5px}
.quick-links li{height:30.5px;display:flex;gap:18px}
.quick-links li::before{content:"»";font-weight:700}
.news-text{left:773px;top:3130px;color:var(--white);font-size:12.5px}
.news-input{left:773px;top:3171px;width:235px;height:36px;background:var(--white);font-size:12px;color:#555;padding:10px 16px}
.news-btn{left:773px;top:3221px;width:105px;height:35px;background:#3b6a8e;color:var(--white);font-weight:700;font-size:14px;display:flex;align-items:center;justify-content:center}
.foot-rule{top:3380px;height:1px;background:#4a6479}
.socials{left:505px;top:3359px;display:flex;gap:7px}
.socials span{width:42px;height:42px;border:2px solid var(--white);border-radius:50%;display:flex;align-items:center;justify-content:center}
.socials span::after{content:"";width:8px;height:8px;border-radius:50%;background:var(--white)}
.copyright{left:143px;top:3417px;color:var(--white);font-size:12px}
.legal{left:832px;top:3417px;color:var(--white);font-size:12px}
.chat{left:1094px;top:3307px;width:66px;height:66px;border-radius:50%;background:#2b5573;display:flex;align-items:center;justify-content:center;box-shadow:0 3px 8px rgba(0,0,0,.3)}
</style>
</head>
<body>

<header>
  <div class="abs brand" style="left:143px;top:34px"><span class="brand-dot"></span><span>Meridale<br>Partners</span></div>
  <div class="abs header-phone">
    <svg width="44" height="44" viewBox="0 0 44 44" aria-hidden="true"><circle cx="22" cy="22" r="20" fill="none" stroke="#1e3d56" stroke-width="3"/><path d="M15 13c2-2 4 0 5 2s0 3-1 4c1 2 3 4 5 5 1-1 2-2 4-1s4 3 2 5c-2 2-5 2-9-1s-7-7-8-10 0-3 2-4z" fill="#1e3d56"/></svg>
    01 555 0142
  </div>
  <div class="abs menu-bars" aria-label="Menu"><span></span><span></span><span></span></div>
</header>

<section class="hero">
  <div class="abs hero-photo" role="img" aria-label="Photo of hands typing on a laptop showing analytics dashboards"></div>
  <h1 class="abs hero-title">Meridale<br>Partners</h1>
  <p class="abs hero-sub">Data Analytics &amp; EPM<br>Consulting Services</p>
  <a class="abs btn hero-btn">Get Started</a>
  <div class="abs slider-dots"><span></span><span class="active"></span><span></span><span></span></div>
</section>

<section>
  <div class="abs about"></div>
  <div class="abs about-art" role="img" aria-label="Circular photo crop of a business team at work"></div>
  <h2 class="abs section-title about-title">About Us</h2>
  <p class="abs about-text">Meridale Partners is an exciting start-up in the Data Analytics and EPM space.&nbsp; Founded in 2019, MP specialise in the implementation and support of BI, EPM and Data Analytics business solutions, both in the Cloud and on-premise.Call us on 01 555 0142 or email: info@meridale-partners.example for more information</p>
  <a class="abs btn about-btn">Read More</a>
</section>

<section>
  <div class="abs wwd-panel" role="img" aria-label="Dark blue digital data background"></div>
  <h2 class="abs section-title wwd-title">What We Do</h2>
  <div class="abs wwd-arrows">
    <svg width="29" height="29" viewBox="0 0 29 29" aria-label="Previous"><circle cx="14.5" cy="14.5" r="12.5" fill="none" stroke="#111" stroke-width="2"/><path d="M21 14.5H9M13.5 9.5l-5 5 5 5" fill="none" stroke="#111" stroke-width="2.4"/></svg>
    <svg width="29" height="29" viewBox="0 0 29 29" aria-label="Next"><circle cx="14.5" cy="14.5" r="12.5" fill="none" stroke="#111" stroke-width="2"/><path d="M8 14.5h12M15.5 9.5l5 5-5 5" fill="none" stroke="#111" stroke-width="2.4"/></svg>
  </div>
  <div class="abs service-card card-advise" role="img" aria-label="Photo of two colleagues reviewing a tablet">Advise &amp; Architect Services</div>
  <div class="abs service-card card-design" role="img" aria-label="Photo of hands at a keyboard with floating interface panels">Design &amp; Implement</div>
  <div class="abs service-card card-optimise" role="img" aria-label="Photo of a tablet with a glowing data visual">Optimise &amp; Manage</div>
</section>

<section>
  <div class="abs how-photo" role="img" aria-label="Photo of a smiling businesswoman in a meeting"></div>
  <div class="abs how-tab"></div>
  <h2 class="abs section-title how-title">How We Do It</h2>
  <div class="abs step" style="top:1833px"><span class="step-mark"></span><span class="step-num">01</span><h3>Analytics</h3><p style="top:28px">Lorem ipsum dolor sit amet consectetur adipiscing elit, sed do eiusmod</p></div>
  <div class="abs step" style="top:1969px"><span class="step-mark"></span><span class="step-num">02</span><h3>Enterprise Performance Management</h3><p style="top:50px">Lorem ipsum dolor sit amet consectetur adipiscing elit, sed do eiusmod</p></div>
  <div class="abs step" style="top:2105px"><span class="step-mark"></span><span class="step-num">03</span><h3>Advisory</h3><p style="top:28px">Lorem ipsum dolor sit amet consectetur adipiscing elit, sed do eiusmod</p></div>
  <div class="abs step" style="top:2241px"><span class="step-mark"></span><span class="step-num">04</span><h3>Consultancy Services</h3><p style="top:28px">Lorem ipsum dolor sit amet consectetur adipiscing elit, sed do eiusmod</p></div>
</section>

<section>
  <div class="abs contact" role="img" aria-label="Faint background of scattered numbers and a dotted data wave"></div>
  <h2 class="abs section-title contact-title">Contact Us</h2>
  <div class="abs field" style="left:234px;top:2593px;width:359px;height:53px">First Name</div>
  <div class="abs field" style="left:605px;top:2593px;width:360px;height:53px">Last Name</div>
  <div class="abs field" style="left:234px;top:2658px;width:359px;height:53px">Email address</div>
  <div class="abs field" style="left:605px;top:2658px;width:360px;height:53px">Phone Number</div>
  <div class="abs field" style="left:234px;top:2723px;width:731px;height:115px">Message</div>
  <a class="abs btn submit">Submit</a>
</section>

<footer>
  <div class="abs footer"></div>
  <div class="abs brand" style="left:177px;top:3085px"><span class="brand-dot"></span><span>Meridale<br>Partners</span></div>
  <div class="abs foot-contact">
    <svg width="42" height="42" viewBox="0 0 44 44" aria-hidden="true"><circle cx="22" cy="22" r="20" fill="none" stroke="#fff" stroke-width="3"/><path d="M15 13c2-2 4 0 5 2s0 3-1 4c1 2 3 4 5 5 1-1 2-2 4-1s4 3 2 5c-2 2-5 2-9-1s-7-7-8-10 0-3 2-4z" fill="#fff"/></svg>
    <div><small>Contact Us</small><strong>01 555 0142</strong></div>
  </div>
  <p class="abs foot-address">14 Harbour Row,<br>Quayside, Dublin 4, D04 KX21<br><a>info@meridale-partners.example</a></p>
  <h4 class="abs foot-heading" style="left:528px;top:3087px">Quick Links</h4>
  <ul class="abs quick-links"><li>Home</li><li>Who we are</li><li>What we do</li><li>How we do it</li><li>Contact</li></ul>
  <h4 class="abs foot-heading" style="left:773px;top:3087px">Sign Up Newsletter</h4>
  <p class="abs news-text">Lorem ipsum dolor sit ameonsectetur adip</p>
  <div class="abs news-input">Enter Email</div>
  <div class="abs news-btn">SIGN UP</div>
  <div class="abs foot-rule" style="left:143px;width:340px"></div>
  <div class="abs foot-rule" style="left:715px;width:340px"></div>
  <div class="abs socials" aria-label="Social links"><span></span><span></span><span></span><span></span></div>
  <p class="abs copyright">Copyright © 2022 Meridale Partners. All rights reserved.</p>
  <p class="abs legal">Terms of use &nbsp;|&nbsp; Privacy policy &nbsp;|&nbsp; Site map</p>
  <div class="abs chat" aria-label="Chat">
    <svg width="28" height="26" viewBox="0 0 28 26" aria-hidden="true"><path d="M2 3h18v13H7l-5 4z" fill="#fff"/><path d="M22 8h4v16l-5-4H9v-2h13z" fill="#fff"/></svg>
  </div>
</footer>

</body>
</html>
```